Specialised investor in e-mobility and energy wants business card design

We need a business card design that fits our existing corporate design. <The look and feel must be 'sharp'/'clean', dynamic, communicate momentum, professionalism etc (as one would imagine from a firm in the financial sector). We like the idea of a reverse-side of the card that includes the logo, and the name and contact details on the other. We expect the deliverable to be whatever format might be required to be able to get cards printed directly by a service such as kelmo press. Our website is www.zub.capital

```html
<!DOCTYPE html>
<html lang="en">
<head>
<meta charset="utf-8">
<title>Zub Capital – Business Card</title>
<link href="https://fonts.googleapis.com/css2?family=Montserrat:wght@400;500;700;800&display=swap" rel="stylesheet">
<style>
  :root{
    --bg:#1f1f1f;
    --forest:#33502a;
    --leaf:#7fb24a;
    --rule:#6d9a3f;
    --paper:#ffffff;
    --ink:#f2f5ee;
  }
  *{box-sizing:border-box;margin:0;padding:0}
  html,body{width:1200px;height:988px;overflow:hidden;background:var(--bg)}
  body{position:relative;font-family:"Montserrat",sans-serif}
  .card{
    position:absolute;width:580px;height:332px;border-radius:22px;overflow:hidden;
    box-shadow:0 10px 30px rgba(0,0,0,.45);
  }
  .card--front{left:70px;top:80px;background:var(--forest);display:flex;align-items:center;justify-content:center}
  .brand{display:flex;align-items:center;gap:16px;color:var(--paper);font-weight:500;font-size:58px;letter-spacing:.5px}
  .brand__dot{width:26px;height:26px;border-radius:50%;background:var(--leaf)}
  .card--back{left:550px;top:576px;background:var(--forest);display:flex}
  .back__band{width:190px;background:var(--paper);position:relative}
  .back__band .brand{
    position:absolute;left:50%;top:50%;transform:translate(-50%,-50%) rotate(-90deg);
    color:var(--forest);font-size:40px;white-space:nowrap;gap:12px
  }
  .back__band .brand__dot{width:18px;height:18px}
  .back__info{flex:1;padding:48px 40px 0 42px;color:var(--ink)}
  .person__name{color:var(--leaf);font-weight:800;font-size:27px;letter-spacing:1px;text-transform:uppercase}
  .person__role{font-size:15px;margin-top:2px}
  .divider{height:1px;background:var(--rule);margin:14px 0 12px;width:300px}
  .contact{list-style:none;font-size:15px;line-height:26px}
  .contact li{display:flex;align-items:center;gap:12px}
  .contact svg{width:13px;height:13px;fill:var(--leaf);flex:none}
  .address{font-size:15px;line-height:22px}
</style>
</head>
<body>
  <section class="card card--front">
    <div class="brand"><span class="brand__dot"></span><span class="brand__name">zub capital</span></div>
  </section>

  <section class="card card--back">
    <div class="back__band">
      <div class="brand"><span class="brand__dot"></span><span class="brand__name">zub capital</span></div>
    </div>
    <div class="back__info">
      <h1 class="person__name">Marten Kolby</h1>
      <p class="person__role">Director/Founder</p>
      <div class="divider"></div>
      <ul class="contact">
        <li><svg viewBox="0 0 24 24"><path d="M6.6 10.8a15.1 15.1 0 0 0 6.6 6.6l2.2-2.2a1 1 0 0 1 1-.25 11.4 11.4 0 0 0 3.6.57 1 1 0 0 1 1 1V20a1 1 0 0 1-1 1A17 17 0 0 1 3 4a1 1 0 0 1 1-1h3.5a1 1 0 0 1 1 1c0 1.25.2 2.45.57 3.57a1 1 0 0 1-.25 1z"/></svg>123-480-2291</li>
        <li><svg viewBox="0 0 24 24"><path d="M2 5h20v14H2z M2 5l10 8 10-8" /></svg>info@zub.capital</li>
        <li><svg viewBox="0 0 24 24"><circle cx="12" cy="12" r="10"/></svg>www.zub.capital</li>
      </ul>
      <div class="divider"></div>
      <p class="address">1234 Street Name<br>Country Name AB 5748</p>
    </div>
  </section>
</body>
</html>
```